Stonebrace Business Card Design

The Stonebrace Co is an aggregate (crushing) equipment dealer serving Western Canadian provinces. Stonebrace is a distributor of aggregate equipment for different manufacturers.

We are looking to change and update the existing business card which has been used since the existence of the company. A copy of existing card has been attached for reference. The Stonebrace Co logo we want to remain the same and we want the green color to remain the same.

We are wanting something new with a different look. A refreshing card to show a new modern and updated look. No longer wanting to have the manufacturers on the back of the card but something more like our logo on the back of the card with a statement like "Crushing Solutions"

ideas could be:
- card can be different colors on front and back
- front or reverse of the card could possibly be the green color with the logo in black

Target Market(s)

Owners of Aggregate/Crushing companies

Contact Information for Business Card

see above

Requirements
Must have
• - logo to remain same along with same font within logo
• - green color to remain same
Nice to have
• as noted above under project description
Should not have

```html
<!DOCTYPE html>
<html lang="en">
<head>
<meta charset="utf-8">
<title>The Stonebrace Co. – Business Card</title>
<link rel="stylesheet" href="https://fonts.googleapis.com/css2?family=Open+Sans:wght@400;600;700&family=Raleway:wght@400&display=swap">
<style>
  :root {
    --olive: #8f8c33;
    --charcoal: #231f20;
    --paper: #ffffff;
    --backdrop: #e4e4e2;
    --ink: #1e1e1e;
  }
  * { box-sizing: border-box; margin: 0; padding: 0; }
  html, body { width: 1200px; height: 1000px; overflow: hidden; }
  body {
    background: var(--backdrop);
    position: relative;
    font-family: "Open Sans", Arial, sans-serif;
  }
  .card {
    position: absolute;
    width: 634px;
    height: 362px;
    border-radius: 40px;
    overflow: hidden;
  }

  /* Front */
  .card-front { left: 148px; top: 100px; background: var(--paper); }
  .front-frame {
    position: absolute;
    left: 25px; top: 28px;
    width: 584px; height: 306px;
    border: 3px solid var(--olive);
    border-radius: 32px;
  }
  .front-mark {
    position: absolute;
    left: 272px; top: 92px;
    width: 90px; height: 90px;
    border-radius: 50%;
    background: var(--olive);
  }
  .front-name {
    position: absolute;
    left: 0; right: 0; top: 222px;
    text-align: center;
    font-weight: 700;
    font-size: 33px;
    letter-spacing: 0.5px;
    color: var(--ink);
  }
  .front-tagline {
    position: absolute;
    left: 50%; top: 311px;
    transform: translateX(-50%);
    padding: 0 18px;
    background: var(--paper);
    font-family: "Raleway", Arial, sans-serif;
    font-size: 23px;
    letter-spacing: 0.5px;
    color: var(--ink);
    white-space: nowrap;
  }

  /* Back */
  .card-back { left: 376px; top: 548px; background: var(--charcoal); }
  .back-brand {
    position: absolute;
    left: 0; top: 0;
    width: 317px; height: 362px;
    background: var(--olive);
    color: var(--paper);
  }
  .back-mark {
    position: absolute;
    left: 138px; top: 106px;
    width: 42px; height: 42px;
    border-radius: 50%;
    background: var(--paper);
  }
  .back-name {
    position: absolute;
    left: 0; right: 0; top: 172px;
    text-align: center;
    font-weight: 700;
    font-size: 21px;
  }
  .back-divider {
    position: absolute;
    left: 0; right: 0; top: 216px;
    border-top: 2px solid rgba(255,255,255,0.75);
  }
  .back-lines {
    position: absolute;
    left: 0; right: 0; top: 238px;
    display: flex;
    justify-content: center;
    font-size: 14.5px;
    letter-spacing: 0.3px;
  }
  .back-lines span { padding: 0 9px; line-height: 22px; }
  .back-lines span + span { border-left: 1.5px solid var(--paper); }

  .contact {
    position: absolute;
    left: 351px; top: 34px;
    color: var(--paper);
  }
  .contact-name { font-size: 27px; font-weight: 600; letter-spacing: 0.3px; margin-bottom: 18px; }
  .contact-list { list-style: none; }
  .contact-list li {
    display: flex; align-items: center;
    height: 34.5px;
    font-size: 19px;
  }
  .contact-list svg { width: 20px; height: 20px; margin-right: 21px; fill: var(--paper); flex: none; }
  .back-rule {
    position: absolute;
    left: 317px; right: 0; top: 277px;
    border-top: 2.5px solid var(--paper);
  }
  .address {
    position: absolute;
    left: 354px; top: 296px;
    font-size: 15.5px;
    line-height: 25px;
    color: var(--paper);
  }
</style>
</head>
<body>

<section class="card card-front">
  <div class="front-frame"></div>
  <div class="front-mark"></div>
  <div class="front-name">THE STONEBRACE CO.</div>
  <div class="front-tagline">CRUSHING SOLUTIONS</div>
</section>

<section class="card card-back">
  <div class="back-brand">
    <div class="back-mark"></div>
    <div class="back-name">THE STONEBRACE CO.</div>
    <div class="back-divider"></div>
    <div class="back-lines"><span>SCREENERS</span><span>CRUSHERS</span><span>STACKERS</span></div>
  </div>

  <div class="contact">
    <div class="contact-name">DEREK MALLORY</div>
    <ul class="contact-list">
      <li>
        <svg viewBox="0 0 24 24"><path d="M2 8c2-4 18-4 20 0v2h-5V8c-3-1-7-1-10 0v2H2z"/><path d="M5 12h14l2 8H3z"/><circle cx="12" cy="16" r="2.2" fill="#231f20"/></svg>
        780 . 555 . 0142
      </li>
      <li>
        <svg viewBox="0 0 24 24"><path d="M6.6 10.8a15 15 0 0 0 6.6 6.6l2.2-2.2c.3-.3.7-.4 1-.2 1.1.4 2.3.6 3.6.6.6 0 1 .4 1 1V20c0 .6-.4 1-1 1A17 17 0 0 1 3 4c0-.6.4-1 1-1h3.5c.6 0 1 .4 1 1 0 1.3.2 2.5.6 3.6.1.3 0 .7-.2 1z"/></svg>
        780 . 555 . 0187
      </li>
      <li>
        <svg viewBox="0 0 24 24"><rect x="6" y="2" width="12" height="6"/><path d="M3 9h18v8h-3v-3H6v3H3z"/><rect x="7" y="15" width="10" height="7"/></svg>
        780 . 555 . 0163
      </li>
      <li>
        <svg viewBox="0 0 24 24"><path d="M3 6h18v1l-9 6-9-6z"/><path d="M3 9l9 6 9-6v9H3z"/></svg>
        derek@stonebr.com
      </li>
      <li>
        <svg viewBox="0 0 24 24"><path d="M12 2a10 10 0 1 0 0 20 10 10 0 0 0 0-20zm0 2c.9 0 2.3 2 2.8 5H9.2C9.7 6 11.1 4 12 4zM4.3 9h2.9a18 18 0 0 0 0 6H4.3a8 8 0 0 1 0-6zm4.9 0h5.6a16 16 0 0 1 0 6H9.2a16 16 0 0 1 0-6zm7.6 0h2.9a8 8 0 0 1 0 6h-2.9a18 18 0 0 0 0-6zM9.2 17h5.6c-.5 3-1.9 5-2.8 5s-2.3-2-2.8-5z"/></svg>
        www.stonebrace.ca
      </li>
    </ul>
  </div>
  <div class="back-rule"></div>
  <address class="address" style="font-style:normal">
    2218-48B AVENUE,<br>
    NISKU, ALBERTA T 9X 1K7
  </address>
</section>

</body>
</html>
```